Luxury Wine Label for New Startup Winery

We need a wine label for our new winery startup. We have worked with a local designer but do not feel the resulting label / logo have the elevation required to present our brand as a luxury wine. Our winery is called "Quailbrook Vineyards" and we are focused on extremely high quality hand crafted artisan and estate wines from the Pacific Northwest.
We would like to see designs that utilize a tree line, or other imagery that represents the "Quailbrook" part of our company name. Another interesting feature could be wood grain.
A logo will be required based on your design so please design with this in mind:
This logo should be consistent with the wine bottle label design, and should be representative of our high end exclusive wine while giving a sense of place (Oregon/ Pacific Northwest.)
I will supply an image of the design we received from our local designer, PLEASE NOTE: in general we do like wood grain and tree line concepts but feel the execution was poorly done.
ATTN: Logo design should be suitable for use on: Bottles (Red wine/rose/white wine), Bussiness cards, vehicle signage, business signage, etc
P.S.:
If you have a design that is not outside the box we are still interested in seeing it.
Label is for a burgundy style bottle with a label height of 3.5 - 4" and a width of 3.5-4"
any label <= 4"x4" and >=3.5"x3.5" will be acceptable:
HOWEVER Width should be greater than or equal to height due to the bottle format
Target Market(s)
Wine enthusiasts with adequate discretionary budgets to afford $100 bottles of wine.
Industry/Entity Type
Wine / Winery
Requirements
Must have
- A sense of luxury, a feel of exclusivity, and a theme consistent with our product and brand name
Nice to have
- Tree line, wood grain or other wood themes. Serif fonts
Should not have
- anything cheesy, off topic, hard to read script fonts or anything that makes the label hard to read from a few feet away or too busy

```html
<!DOCTYPE html>
<html lang="en">
<head>
<meta charset="utf-8">
<title>Quailbrook Vineyards – Syrah Label</title>
<link rel="stylesheet" href="https://fonts.googleapis.com/css2?family=Cormorant+Garamond:ital,wght@0,500;0,600;1,600&family=Montserrat:wght@400&display=swap">
<style>
  :root {
    --backdrop: #e9e4dc;
    --label-black: #121519;
    --gold: #c6a45a;
    --gold-bright: #d9bc4a;
    --ivory: #ece6da;
    --silver: #cfd2d4;
    --wood-dark: #3a2418;
    --wood-mid: #5e3b27;
    --wood-light: #7a5036;
  }
  * { box-sizing: border-box; margin: 0; padding: 0; }
  html, body {
    width: 933px;
    height: 1200px;
    overflow: hidden;
    background: var(--backdrop);
  }
  .label {
    position: absolute;
    left: 56px;
    top: 200px;
    width: 820px;
    height: 800px;
    background: var(--label-black);
  }
  .label-frame {
    position: absolute;
    left: 12px;
    top: 12px;
    width: 796px;
    height: 776px;
    border: 2px solid var(--gold);
  }
  .brand-name,
  .brand-sub,
  .varietal,
  .appellation,
  .estate-line {
    position: absolute;
    left: 0;
    width: 100%;
    text-align: center;
    white-space: nowrap;
  }
  .brand-name {
    top: 58px;
    font-family: "Cormorant Garamond", serif;
    font-weight: 500;
    font-size: 72px;
    line-height: 80px;
    color: var(--ivory);
    letter-spacing: 1px;
  }
  .brand-sub {
    top: 146px;
    font-family: "Montserrat", sans-serif;
    font-weight: 400;
    font-size: 26px;
    line-height: 32px;
    color: var(--silver);
    letter-spacing: 9px;
    padding-left: 9px;
  }
  .landscape {
    position: absolute;
    left: 14px;
    top: 200px;
    width: 792px;
    height: 186px;
    background: linear-gradient(180deg, #14171b 0%, #1c2025 40%, #2c3034 65%, #6e7275 86%, #1a1d21 100%);
  }
  .rule {
    position: absolute;
    left: 14px;
    width: 792px;
  }
  .rule-upper { top: 408px; height: 2px; background: var(--gold); }
  .rule-lower { top: 516px; height: 4px; background: var(--gold-bright); }
  .varietal {
    top: 430px;
    font-family: "Cormorant Garamond", serif;
    font-style: italic;
    font-weight: 600;
    font-size: 58px;
    line-height: 66px;
    color: var(--ivory);
  }
  .wood-panel {
    position: absolute;
    left: 14px;
    top: 520px;
    width: 792px;
    height: 266px;
    background: linear-gradient(175deg, var(--wood-mid) 0%, var(--wood-light) 20%, var(--wood-dark) 42%, var(--wood-mid) 60%, var(--wood-light) 78%, var(--wood-dark) 100%);
  }
  .appellation,
  .estate-line {
    font-family: "Cormorant Garamond", serif;
    font-weight: 600;
    color: var(--ivory);
    letter-spacing: 1px;
    font-variant-numeric: lining-nums;
    font-feature-settings: "lnum" 1;
  }
  .appellation {
    top: 652px;
    font-size: 36px;
    line-height: 42px;
  }
  .estate-line {
    top: 716px;
    font-size: 30px;
    line-height: 36px;
  }
</style>
</head>
<body>
  <div class="label">
    <div class="label-frame"></div>
    <div class="brand-name">Quailbrook</div>
    <div class="brand-sub">VINEYARDS</div>
    <div class="landscape" role="img" aria-label="Engraved silver line illustration of rolling hills with a tree line"></div>
    <div class="rule rule-upper"></div>
    <div class="varietal">Syrah</div>
    <div class="rule rule-lower"></div>
    <div class="wood-panel" role="img" aria-label="Dark walnut wood grain texture"></div>
    <div class="appellation">WILLAMETTE VALLEY 2023</div>
    <div class="estate-line">ESTATE GROWN · OREGON TERROIR</div>
  </div>
</body>
</html>
```